Cobalt Ridge Electric Needs A Logo Design

We need a logo for my new company based out of Sacramento, Ca called Cobalt Ridge Electric. The name says it all, my electrical contracting business provides "Cobalt Ridge Professional Work" I'm open to any colors that pop and customers to say Wow. I would love to print my cards on metal.

Industry/Entity Type

Business

Contact Information for Business Card

The card needs to have as follows
Name of company: Cobalt Ridge Electric
My Name: Marco Delvane
Phone # 916-555-0173
CL# 2049381
Email: cobaltridgeelectric@mailnest.example
and a slogan that represent "COBALT RIDGE"

Requirements
Must have
• The card needs to have as follows
• Name of company: Cobalt Ridge Electric
• My Name : Marco Delvane
• Phone # 916-555-0173
• CL# 2049381
• Email: cobaltridgeelectric@mailnest.example
• and a slogan that represent "COBALT RIDGE"
Nice to have
• popping colors
• electrical Arcing

```html
<!DOCTYPE html>
<html lang="en">
<head>
<meta charset="utf-8">
<title>Cobalt Ridge Electric – Business Cards</title>
<link rel="stylesheet" href="https://fonts.googleapis.com/css2?family=Open+Sans:wght@400;600;700&display=swap">
<style>
  :root {
    --cobalt: #0b86ad;
    --cobalt-deep: #0a7398;
    --paper: #f7f7f7;
    --white: #ffffff;
    --amber: #ee9a1d;
    --rule-grey: #9aa3a8;
    --backdrop: #e6e3de;
  }
  * { box-sizing: border-box; margin: 0; padding: 0; }
  html, body {
    width: 1200px;
    height: 900px;
    overflow: hidden;
  }
  body {
    background: var(--backdrop);
    font-family: "Open Sans", Arial, sans-serif;
    display: flex;
    flex-direction: column;
    align-items: center;
    justify-content: center;
    gap: 56px;
  }
  .card {
    position: relative;
    width: 600px;
    height: 343px;
    overflow: hidden;
    box-shadow: 0 6px 18px rgba(0, 0, 0, 0.18);
  }

  /* Brand lockup: one colour, one weight, plain square */
  .brand {
    position: absolute;
    display: flex;
    align-items: center;
    gap: 16px;
    left: 0;
    right: 0;
    justify-content: center;
  }
  .brand-square {
    width: 30px;
    height: 30px;
    flex: none;
  }
  .brand-name {
    font-weight: 600;
    font-size: 30px;
    letter-spacing: 1.5px;
    text-transform: uppercase;
    white-space: nowrap;
  }

  /* Card back */
  .card-back { background: var(--cobalt); }
  .card-back .brand { top: 92px; }
  .card-back .brand-square { background: var(--white); }
  .card-back .brand-name { color: var(--white); }
  .slogan-band {
    position: absolute;
    left: 0;
    right: 0;
    top: 196px;
    height: 74px;
    background: var(--white);
    display: flex;
    align-items: flex-end;
    justify-content: center;
    padding-bottom: 14px;
  }
  .slogan {
    color: var(--cobalt);
    font-weight: 700;
    font-size: 15px;
    letter-spacing: 0.6px;
    text-transform: uppercase;
  }

  /* Card front */
  .card-front { background: var(--cobalt); }
  .front-top {
    position: absolute;
    left: 0;
    right: 0;
    top: 0;
    height: 188px;
    background: var(--paper);
    border-bottom: 4px solid var(--amber);
  }
  .card-front .brand { top: 78px; }
  .card-front .brand-square { background: var(--amber); }
  .card-front .brand-name { color: var(--cobalt); }
  .brand-rule {
    position: absolute;
    top: 124px;
    left: 150px;
    right: 150px;
    height: 1px;
    background: var(--rule-grey);
  }

  .contact-list {
    position: absolute;
    top: 214px;
    right: 250px;
    list-style: none;
    text-align: right;
    color: var(--white);
    font-size: 14px;
    line-height: 24px;
  }
  .contact-list li {
    display: flex;
    align-items: center;
    justify-content: flex-end;
    gap: 8px;
  }
  .contact-list svg { width: 13px; height: 13px; fill: var(--white); }
  .person-name {
    position: absolute;
    top: 212px;
    left: 372px;
    color: var(--white);
    font-weight: 600;
    font-size: 17px;
  }
  .email {
    position: absolute;
    top: 292px;
    left: 0;
    right: 0;
    text-align: center;
    color: var(--white);
    font-size: 17px;
    letter-spacing: 0.2px;
  }
</style>
</head>
<body>

  <section class="card card-back" aria-label="Card back">
    <div class="brand">
      <span class="brand-square"></span>
      <span class="brand-name">Cobalt Ridge Electric</span>
    </div>
    <div class="slogan-band">
      <p class="slogan">Cobalt Ridge Professional Work</p>
    </div>
  </section>

  <section class="card card-front" aria-label="Card front">
    <div class="front-top">
      <div class="brand">
        <span class="brand-square"></span>
        <span class="brand-name">Cobalt Ridge Electric</span>
      </div>
      <div class="brand-rule"></div>
    </div>

    <ul class="contact-list">
      <li>916-555-0173
        <svg viewBox="0 0 24 24" aria-hidden="true"><path d="M6.6 10.8a15 15 0 0 0 6.6 6.6l2.2-2.2a1 1 0 0 1 1-.25 11.4 11.4 0 0 0 3.6.57 1 1 0 0 1 1 1V20a1 1 0 0 1-1 1A17 17 0 0 1 3 4a1 1 0 0 1 1-1h3.5a1 1 0 0 1 1 1c0 1.25.2 2.45.57 3.57a1 1 0 0 1-.25 1z"/></svg>
      </li>
      <li>2049381
        <svg viewBox="0 0 24 24" aria-hidden="true"><path d="M7 1h10a2 2 0 0 1 2 2v18a2 2 0 0 1-2 2H7a2 2 0 0 1-2-2V3a2 2 0 0 1 2-2zm0 3v14h10V4zm5 15.5a1.2 1.2 0 1 0 0 2.4 1.2 1.2 0 0 0 0-2.4z"/></svg>
      </li>
      <li>
        <svg viewBox="0 0 24 24" aria-hidden="true"><path d="M2 5h20v14H2zm2 2v.5l8 5 8-5V7zm0 2.9V17h16V9.9l-8 5z"/></svg>
      </li>
    </ul>
    <p class="person-name">Marco Delvane</p>
    <p class="email">cobaltridgeelectric@mailnest.example</p>
  </section>

</body>
</html>
```